Vernac Law Business cards and stationary design project

We are looking for a stationary design for business cards (double sided), 8x10, 5x7, and legal and standard envelopes.

We would like the design to match the logo that we have already.
Color palate preferred is Teal, White, grey and any others that will look good for a professional law firm.

We would like this statement: "RELATIONSHIPS. RESPECT. RESULT" to be on the back of the business cards and maybe on the stationary if it looks good.

Please see link to website for more information: www.vernac-law.example

Target Market(s)

Potential clients that need Attorney services.

Industry/Entity Type

Law Firm

Contact Information for Business Card

We would like the front and back to be two different colors. Current business cards are teal front, grey back and are a vertical design. We are open to options with colors.

Font styles to use
Serif

Colors
33a6d7
33b8a4
b9b9b9
5c5c5c

Requirements
Must have
• Logo supplied needs to go on the card and stationary.
• Match website color palate, www.vernac-law.example
• Be professional and not too wordy.
• Criminal Law, Civil Litigation, Personal Injury, Restraining Orders need to be on the card.
Nice to have
• RELATIONSHIPS. RESPECT. RESULTS. on the back of the card.
Should not have
• Not be too busy/wordy or too flashy.

```html
<!DOCTYPE html>
<html lang="en">
<head>
<meta charset="utf-8">
<title>Vernac Law – Business Card</title>
<link rel="stylesheet" href="https://fonts.googleapis.com/css2?family=Cinzel:wght@400;500&family=Tinos:wght@400;700&display=swap">
<style>
  :root {
    --backdrop: #3b3b3b;
    --teal: #0f8796;
    --slate: #6e6e6e;
    --ink: #ffffff;
    --rule: rgba(255,255,255,0.85);
  }
  * { box-sizing: border-box; margin: 0; padding: 0; }
  html, body {
    width: 1105px;
    height: 1200px;
    overflow: hidden;
    background: var(--backdrop);
  }
  .card {
    position: absolute;
    left: 196px;
    width: 720px;
    height: 412px;
    color: var(--ink);
    text-align: center;
  }
  .card--front { top: 145px; background: var(--teal); }
  .card--back  { top: 602px; background: var(--slate); }
  .card__frame {
    position: absolute;
    inset: 21px;
    border: 4px solid var(--ink);
  }
  .row {
    position: absolute;
    left: 0;
    right: 0;
    line-height: 1;
  }
  .name {
    top: 76px;
    font-family: "Cinzel", serif;
    font-size: 33px;
    font-weight: 500;
    letter-spacing: 0.5px;
  }
  .title {
    top: 114px;
    font-family: "Cinzel", serif;
    font-size: 20px;
    letter-spacing: 1px;
  }
  .divider {
    position: absolute;
    left: 160px;
    width: 405px;
    border-top: 2px dotted var(--rule);
  }
  .divider--top { top: 153px; }
  .divider--bottom { top: 251px; }
  .contact {
    font-family: "Tinos", serif;
    font-size: 20px;
  }
  .contact b { font-weight: 700; }
  .contact--main { top: 179px; }
  .contact--web { top: 210px; }
  .practice {
    font-family: "Tinos", serif;
    font-size: 19px;
  }
  .practice--criminal { top: 272px; }
  .practice--civil { top: 298px; }
  .tagline {
    top: 326px;
    font-family: "Cinzel", serif;
    font-size: 21px;
    letter-spacing: 0.6px;
  }
  .firm {
    top: 184px;
    font-family: "Cinzel", serif;
    font-size: 46px;
    font-weight: 400;
    letter-spacing: 1.5px;
  }
</style>
</head>
<body>
  <section class="card card--front" aria-label="Business card front">
    <div class="card__frame"></div>
    <p class="row name">Maren Vernac</p>
    <p class="row title">Trial Lawyer</p>
    <div class="divider divider--top"></div>
    <p class="row contact contact--main"><b>P:</b> (555) 010-4821&nbsp;&nbsp;<b>E:</b> maren@vernac-law.example</p>
    <p class="row contact contact--web"><b>W:</b> www.vernac-law.example</p>
    <div class="divider divider--bottom"></div>
    <p class="row practice practice--criminal">Criminal Law</p>
    <p class="row practice practice--civil">Civil Litigation/Personal Injury, Restraining</p>
    <p class="row tagline">RELATIONSHIPS. RESPECT. RESULTS.</p>
  </section>

  <section class="card card--back" aria-label="Business card back">
    <div class="card__frame"></div>
    <p class="row firm">Vernac Law</p>
  </section>
</body>
</html>
```